Velour Detailing – Premium Automotive Detailing Studio Website Design

We're launching a premium automotive detailing studio called Velour Detailing, and we’re looking for a clean, minimal, and high-end website design (desktop + mobile version). The studio targets owners of luxury vehicles who care deeply about aesthetics, perfection, and exceptional service.
This project is about more than just showing services , it should feel like a luxury experience from the very first second. The design should be modern, minimalistic, elegant, and clearly aimed at an upscale market.
We’re looking for a designer who can translate our physical studio’s premium interior and architectural feel into a digital presence.
What we want the website to feel like:
Clean and modern
Professional and luxurious
Minimal and not cluttered
Light animations or transitions to add polish
Stylish and cinematic
Design freedom:
We trust your design direction. We are not providing strict color codes or layout instructions, we want you to create what you believe works best based on our brand positioning and target audience. Just keep it premium, modern, and well-organized.
What the website should include:
Hero section with a bold visual (image or video)
About the Studio — a few blocks explaining our story and focus on quality
Service Overview — clearly showing what we offer (detailing, ceramic coating, interior, etc.)
Gallery/Showcase — show off our work with cars, interior, and the space itself
Client Lounge Area — mention comfort, coffee, and waiting space
Testimonials — social proof from satisfied clients
Location & contact section — map, address, contact form
Footer, simple with nav, contact info, and optional social media
Target audience:
Owners of high-end vehicles (Valtrane, Korvel, etc.)
Car collectors and detailing enthusiasts
People looking for premium-level service and presentation
Brands/creators booking our photo studio

```html
<!DOCTYPE html>
<html lang="en">
<head>
<meta charset="utf-8">
<title>Velour Detailing</title>
<link href="https://fonts.googleapis.com/css2?family=Krona+One&family=Poppins:wght@300;400;500;600&display=swap" rel="stylesheet">
<style>
:root{
  --black:#000;
  --ink:#0b0b0b;
  --charcoal:#1c1c1c;
  --white:#fff;
  --gold:#c9a66b;
  --grey-text:#4a4a4a;
  --light-text:#cfcfcf;
  --field:#f1f1f1;
  --map:#e4e4e4;
  --red:#b3151d;
  --ember:#e8731a;
}
*{margin:0;padding:0;box-sizing:border-box}
html,body{width:1200px;height:5310px;overflow:hidden}
body{background:var(--white);font-family:'Poppins',sans-serif;color:var(--ink);position:relative}
.display{font-family:'Krona One',sans-serif;text-transform:uppercase;line-height:1.05;letter-spacing:3px;font-weight:400}
section,header,footer{position:absolute;left:0;width:1200px}
.abs{position:absolute}
.fill{position:absolute}

/* header */
.site-header{top:0;height:90px;z-index:3}
.brand{position:absolute;left:93px;top:27px;display:flex;align-items:center;gap:10px;color:var(--white);font-family:'Krona One',sans-serif;font-size:15px;letter-spacing:2px}
.brand-mark{width:26px;height:26px;border:2px solid var(--white)}
.nav{position:absolute;top:38px;left:398px}
.nav a{position:absolute;color:var(--white);font-size:10px;font-weight:500;text-decoration:none;white-space:nowrap;letter-spacing:.5px}
.btn-book{position:absolute;left:882px;top:25px;width:190px;height:38px;background:var(--white);color:var(--black);font-size:9px;font-weight:600;display:flex;align-items:center;padding-left:16px;white-space:nowrap}
.btn-book .sq{position:absolute;right:6px;top:6px;width:26px;height:26px;border:2px solid var(--black)}

/* hero */
.hero{top:0;height:746px;overflow:hidden;
  background:
    radial-gradient(ellipse 420px 200px at 50% 22%,rgba(200,30,36,.55) 0%,rgba(120,14,18,.25) 55%,rgba(0,0,0,0) 100%),
    linear-gradient(180deg,#0c0c0c 0%,#181818 55%,#232323 78%,#121212 100%)}
.hero-photo{left:300px;top:140px;width:600px;height:370px;
  background:
    radial-gradient(ellipse 90px 22px at 24% 44%,rgba(235,235,245,.55),rgba(235,235,245,0) 100%),
    radial-gradient(ellipse 90px 22px at 76% 44%,rgba(235,235,245,.55),rgba(235,235,245,0) 100%),
    radial-gradient(ellipse 150px 60px at 50% 55%,rgba(30,30,30,.9),rgba(30,30,30,0) 100%),
    radial-gradient(ellipse 300px 170px at 50% 45%,#c4171f 0%,#7a0c12 55%,rgba(20,20,20,0) 100%),
    radial-gradient(ellipse 320px 40px at 50% 92%,rgba(0,0,0,.85),rgba(0,0,0,0) 100%)}
.hero-floor{left:0;top:470px;width:1200px;height:276px;background:linear-gradient(180deg,rgba(0,0,0,0),rgba(0,0,0,.55))}
.hero-title{position:absolute;color:var(--white);font-size:56px;white-space:nowrap;line-height:1}
.play{position:absolute;left:205px;top:644px;width:62px;height:62px;border:2px solid var(--white);border-radius:50%;display:flex;align-items:center;justify-content:center}

/* shared section titles */
.sec-title{position:absolute;font-size:36px}
.bar{position:absolute;width:3px;background:var(--gold)}

/* services */
.services{top:746px;height:614px;background:var(--charcoal);overflow:hidden}
.services .sec-title{left:89px;top:200px;color:var(--white)}
.services .bar{left:72px;top:203px;height:110px}
.services .lead{position:absolute;left:89px;top:339px;color:var(--light-text);font-size:12px;line-height:1.6;width:260px}
.mini-arrow{position:absolute;width:36px;height:36px;display:flex;align-items:center;justify-content:center;color:var(--white);font-size:12px}
.card-photo{position:absolute}
.card-interior{left:462px;top:136px;width:451px;height:314px;
  background:
    radial-gradient(ellipse 110px 40px at 48% 52%,rgba(205,165,110,.7),rgba(205,165,110,0) 100%),
    radial-gradient(ellipse 200px 70px at 48% 55%,#0e0e0e 0%,rgba(14,14,14,.6) 60%,rgba(14,14,14,0) 100%),
    radial-gradient(ellipse 230px 14px at 48% 82%,rgba(0,0,0,.8),rgba(0,0,0,0) 100%),
    linear-gradient(180deg,#2d2d2d 0%,#262626 60%,#2f2f2f 100%)}
.card-ceramic{left:938px;top:155px;width:262px;height:276px;
  background:
    radial-gradient(ellipse 120px 45px at 80% 55%,#bdbdbd 0%,#7d7d7d 55%,rgba(60,60,60,0) 100%),
    radial-gradient(ellipse 140px 12px at 80% 78%,rgba(0,0,0,.8),rgba(0,0,0,0) 100%),
    linear-gradient(180deg,#2b2b2b,#262626)}
.card-frame{position:absolute;left:455px;top:128px;width:20px;height:330px;border-left:2px solid #5a5a5a;border-bottom:2px solid #5a5a5a}
.card-frame-top{position:absolute;left:890px;top:128px;width:25px;height:20px;border-top:2px solid #5a5a5a;border-right:2px solid #5a5a5a}
.card-label{position:absolute;color:var(--white);font-family:'Krona One',sans-serif;font-size:14px;letter-spacing:1.5px;white-space:nowrap}
.card-desc{position:absolute;color:var(--light-text);font-size:11px;white-space:nowrap}

/* studio */
.studio{top:1360px;height:631px;background:var(--white)}
.studio-photo{left:0;top:0;width:686px;height:631px;
  background:
    radial-gradient(ellipse 250px 110px at 50% 60%,#3c3d42 0%,#232428 60%,rgba(35,36,40,0) 100%),
    radial-gradient(ellipse 330px 30px at 48% 84%,rgba(0,0,0,.7),rgba(0,0,0,0) 100%),
    linear-gradient(180deg,#8c8794 0%,#a69aa2 25%,#7d7785 45%,#57555d 58%,#2e2e31 75%,#3e3e41 100%)}
.studio .sec-title{left:773px;top:178px}
.studio .bar{left:755px;top:180px;height:110px}
.studio p{position:absolute;left:773px;top:302px;width:340px;font-size:12px;line-height:1.7;color:var(--grey-text)}
.btn-dark{position:absolute;left:773px;top:454px;width:195px;height:41px;background:var(--black);color:var(--white);font-size:9px;font-weight:600;display:flex;align-items:center;padding-left:28px}
.btn-dark .sq{position:absolute;right:6px;top:5px;width:30px;height:30px;border:2px solid var(--white);background:var(--black)}
.tag{position:absolute;left:528px;top:552px;color:var(--white);font-family:'Krona One',sans-serif;font-size:11px;line-height:1.5;letter-spacing:1px}
.tag::before{content:"";position:absolute;left:0;top:-12px;width:40px;height:2px;background:var(--gold)}

/* craft */
.craft{top:1991px;height:277px}
.craft .sec-title{left:89px;top:78px}
.craft .bar{left:72px;top:80px;height:74px}
.craft p{position:absolute;left:89px;top:170px;font-size:12px;line-height:1.7;color:var(--grey-text);width:620px}
.arrows{position:absolute;display:flex;gap:4px}
.arrows span{width:36px;height:36px;display:flex;align-items:center;justify-content:center;font-size:12px}
.arrows .a-dark{background:var(--black);color:var(--white)}
.arrows .a-gold{background:var(--gold);color:var(--white)}

.showcase{top:2268px;height:700px;overflow:hidden;
  background:
    radial-gradient(ellipse 330px 160px at 58% 45%,#262626 0%,#111 60%,rgba(17,17,17,0) 100%),
    radial-gradient(ellipse 420px 30px at 56% 76%,rgba(0,0,0,.9),rgba(0,0,0,0) 100%),
    linear-gradient(180deg,#000 0%,#0a0a0a 45%,#2a2a2c 72%,#1a1a1c 100%)}
.showcase .glow{position:absolute;left:0;top:290px;width:1200px;height:60px;background:linear-gradient(90deg,rgba(232,115,26,0) 0%,rgba(232,115,26,.7) 12%,rgba(232,115,26,.25) 40%,rgba(232,115,26,0) 70%);filter:blur(10px)}
.showcase .trim{position:absolute;left:700px;top:505px;width:330px;height:24px;background:radial-gradient(ellipse at 50% 50%,rgba(232,115,26,.6),rgba(232,115,26,0) 70%)}

/* lounge */
.lounge{top:2968px;height:691px}
.lounge .sec-title{left:89px;top:262px}
.lounge .bar{left:72px;top:264px;height:110px}
.lounge p{position:absolute;left:89px;top:402px;width:400px;font-size:12px;line-height:1.7;color:var(--grey-text)}
.lounge-photo{left:588px;top:0;width:478px;height:619px;
  background:
    radial-gradient(ellipse 130px 60px at 60% 72%,rgba(150,110,80,.6),rgba(150,110,80,0) 100%),
    linear-gradient(180deg,#8e9297 0%,#7b8088 30%,#3c4760 48%,#2f3a52 64%,#6b6f75 78%,#a9a5a0 100%)}

/* testimonials */
.testimonials{top:3659px;height:598px}
.testimonials .sec-title{left:89px;top:86px;font-size:34px;white-space:nowrap}
.testimonials .bar{left:72px;top:84px;height:40px}
.quote{position:absolute;width:240px}
.stars{display:flex;gap:4px;margin-bottom:22px}
.quote blockquote{font-size:18px;line-height:1.5;font-weight:400}
.quote cite{display:block;margin-top:22px;font-style:normal;font-family:'Krona One',sans-serif;font-size:12px;letter-spacing:1px}
.quote-card{position:absolute;left:379px;top:171px;width:441px;height:283px;
  background:
    radial-gradient(ellipse 90px 110px at 92% 50%,#3a3a3a 0%,#1c1c1c 60%,rgba(0,0,0,0) 100%),
    linear-gradient(90deg,#000 55%,#141414 100%)}
.quote-card .quote{left:48px;top:70px;color:var(--white)}

/* contact */
.contact{top:4257px;height:546px;z-index:2}
.map{left:0;top:0;width:1200px;height:546px;background:linear-gradient(135deg,#e8e8e8,#dcdcdc)}
.radius{position:absolute;left:763px;top:161px;width:256px;height:256px;border:2px solid #555;border-radius:50%}
.form-card{position:absolute;left:122px;top:113px;width:466px;height:532px;background:var(--white);z-index:2}
.form-card h2{position:absolute;left:0;width:466px;top:60px;text-align:center;font-size:34px}
.field{position:absolute;left:47px;width:371px;height:41px;background:var(--field);font-size:9px;font-weight:600;padding:14px 0 0 20px}
.btn-send{position:absolute;left:47px;top:450px;width:371px;height:37px;background:var(--black);color:var(--white);font-size:9px;font-weight:600;display:flex;align-items:center;justify-content:center}
.btn-send .sq{position:absolute;right:6px;top:4px;width:28px;height:28px;border:2px solid var(--white)}

/* footer */
.site-footer{top:4803px;height:507px;background:var(--black);color:var(--white);z-index:1}
.footer-brand{position:absolute;left:150px;top:165px;width:200px;text-align:center}
.footer-brand .mark{width:100px;height:100px;border:4px solid var(--white);margin:0 auto 18px}
.footer-brand .name{font-family:'Krona One',sans-serif;font-size:20px;letter-spacing:3px;line-height:1.3}
.footer-col{position:absolute;top:224px;list-style:none;font-size:10px;line-height:2.3}
.socials{position:absolute;left:808px;top:227px;display:flex;gap:16px}
.socials span{width:45px;height:45px;border:1px solid #888}
.rule{position:absolute;left:160px;top:437px;width:880px;height:1px;background:#333}
.copy{position:absolute;left:0;width:1200px;top:462px;text-align:center;font-size:10px}
.to-top{position:absolute;left:1134px;top:423px;width:37px;height:37px;background:var(--gold);display:flex;align-items:center;justify-content:center}
</style>
</head>
<body>

<header class="site-header">
  <div class="brand"><span class="brand-mark"></span>VELOUR DETAILING</div>
  <nav class="nav">
    <a style="left:0">ABOUT</a>
    <a style="left:60px">SERVICES</a>
    <a style="left:134px">GALLERY</a>
    <a style="left:200px">CLIENT LOUNGE AREA</a>
    <a style="left:334px">CONTACT US</a>
  </nav>
  <div class="btn-book">BOOK YOUR APPOINTMENT<span class="sq"></span></div>
</header>

<section class="hero">
  <div class="fill hero-photo" role="img" aria-label="Red luxury sports car, front view, in a dark studio"></div>
  <div class="fill hero-floor"></div>
  <h1 class="display hero-title" style="left:90px;top:566px">Where Luxury</h1>
  <h1 class="display hero-title" style="right:88px;top:628px">Meets Precision</h1>
  <div class="play"><svg width="14" height="14" viewBox="0 0 14 14"><path d="M4 2l8 5-8 5z" fill="#fff"/></svg></div>
</section>

<section class="services">
  <span class="bar"></span>
  <h2 class="display sec-title">Our<br>Signature<br>Services</h2>
  <p class="lead">Premium Automotive Detailing for the Discerning Car Owner</p>
  <span class="mini-arrow" style="left:86px;top:413px">‹</span>
  <span class="mini-arrow" style="left:127px;top:413px">›</span>
  <div class="card-photo card-interior" role="img" aria-label="Black luxury saloon with all doors open showing tan leather interior"></div>
  <div class="card-frame"></div>
  <div class="card-frame-top"></div>
  <div class="card-label" style="left:460px;top:472px">INTERIOR DETAILING</div>
  <div class="card-desc" style="left:460px;top:498px">Deep interior cleaning for a spotless, luxurious cabin experience.</div>
  <div class="card-photo card-ceramic" role="img" aria-label="Silver sports coupe in profile"></div>
  <div class="card-label" style="left:938px;top:472px">CERAMIC COATING</div>
  <div class="card-desc" style="left:938px;top:498px">Advanced protection technology for long-lasting</div>
</section>

<section class="studio">
  <div class="fill studio-photo" role="img" aria-label="Dark grey electric grand tourer parked under a dusk sky"></div>
  <div class="tag">BEYOND THE<br>LIMITS</div>
  <span class="bar"></span>
  <h2 class="display sec-title">A Studio<br>Built for<br>Excellence</h2>
  <p>At Velour Detailing, we believe detailing is an art not just a service. Our studio was created for those who value craftsmanship, aesthetics, and flawless execution. From our advanced techniques to our elegant space, every detail reflects our commitment to perfection.</p>
  <div class="btn-dark">BUILD YOUR OWN<span class="sq"></span></div>
</section>

<section class="craft">
  <span class="bar"></span>
  <h2 class="display sec-title">Our Craft<br>In Motion</h2>
  <p>Explore our portfolio of luxury vehicles, client favorites, and behind-the-scenes shots from our detailing studio. Precision, beauty, and dedication — all on display.</p>
  <div class="arrows" style="left:1031px;top:117px"><span class="a-dark">‹</span><span class="a-gold">›</span></div>
</section>

<section class="showcase" role="img" aria-label="Black Valtrane coupe with orange accent light streak in a dark studio">
  <div class="glow"></div>
  <div class="trim"></div>
</section>

<section class="lounge">
  <span class="bar"></span>
  <h2 class="display sec-title">Relax While<br>We Perfect<br>Your Vehicle</h2>
  <p>Our private client lounge is designed for your comfort. Enjoy freshly brewed coffee, fast Wi-Fi, and a quiet, stylish space while your car receives our full attention.</p>
  <div class="fill lounge-photo" role="img" aria-label="Client lounge with navy booth seating, wooden table and clients relaxing"></div>
</section>

<section class="testimonials">
  <span class="bar"></span>
  <h2 class="display sec-title">What Our Clients Say</h2>
  <div class="arrows" style="left:1029px;top:86px"><span class="a-dark">‹</span><span class="a-gold">›</span></div>

  <div class="quote" style="left:89px;top:240px">
    <div class="stars">
      <svg width="112" height="20" viewBox="0 0 112 20"><g fill="none" stroke="#000" stroke-width="1.2"><path id="s" d="M10 2l2.4 5.2 5.6.6-4.2 3.8 1.2 5.6L10 14.4 5 17.2l1.2-5.6L2 7.8l5.6-.6z"/><use href="#s" x="22"/><use href="#s" x="44"/><use href="#s" x="66"/><use href="#s" x="88"/></g></svg>
    </div>
    <blockquote>“Velour Detailing is in a league of its own. My Korvel has never.”</blockquote>
    <cite>— IDRIS K.</cite>
  </div>

  <div class="quote-card" role="img" aria-label="Dark card with the front of a black sports car on the right">
    <div class="quote">
      <div class="stars">
        <svg width="112" height="20" viewBox="0 0 112 20"><g fill="#fff"><path id="f" d="M10 2l2.4 5.2 5.6.6-4.2 3.8 1.2 5.6L10 14.4 5 17.2l1.2-5.6L2 7.8l5.6-.6z"/><use href="#f" x="22"/><use href="#f" x="44"/><use href="#f" x="66"/><use href="#f" x="88"/></g></svg>
      </div>
      <blockquote>“Every time I visit, it feels like a luxury experience not just car care.”</blockquote>
      <cite>— LENA V.</cite>
    </div>
  </div>

  <div class="quote" style="left:893px;top:240px">
    <div class="stars">
      <svg width="112" height="20" viewBox="0 0 112 20"><g fill="none" stroke="#000" stroke-width="1.2"><path id="t" d="M10 2l2.4 5.2 5.6.6-4.2 3.8 1.2 5.6L10 14.4 5 17.2l1.2-5.6L2 7.8l5.6-.6z"/><use href="#t" x="22"/><use href="#t" x="44"/><use href="#t" x="66"/><use href="#t" x="88"/></g></svg>
    </div>
    <blockquote>“They treated my car like a work of art. I won’t go anywhere else.”</blockquote>
    <cite>— MARCO T.</cite>
  </div>
</section>

<section class="contact">
  <div class="fill map" role="img" aria-label="Greyscale city map showing the studio location"></div>
  <div class="radius"></div>
  <svg class="abs" style="left:876px;top:262px" width="32" height="44" viewBox="0 0 32 44"><path d="M16 0C7 0 0 7 0 16c0 12 16 28 16 28s16-16 16-28C32 7 25 0 16 0z" fill="#000"/><circle cx="16" cy="15" r="6" fill="#fff"/></svg>
  <div class="form-card">
    <h2 class="display">Get In Touch</h2>
    <div class="field" style="top:118px">NAME</div>
    <div class="field" style="top:167px">EMAIL</div>
    <div class="field" style="top:217px">PHONE</div>
    <div class="field" style="top:266px">VEHICLE TYPE</div>
    <div class="field" style="top:316px;height:95px">MESSAGE</div>
    <div class="btn-send">SEND INQUIRY<span class="sq"></span></div>
  </div>
</section>

<footer class="site-footer">
  <div class="footer-brand"><div class="mark"></div><div class="name">VELOUR<br>DETAILING</div></div>
  <ul class="footer-col" style="left:418px">
    <li>About</li><li>Our Services</li><li>Gallery</li><li>Client Lounge Area</li><li>Contact Us</li>
  </ul>
  <ul class="footer-col" style="left:592px">
    <li>+1 555 0142 766</li><li>hello@velourstudio.example</li><li>www.velourstudio.example</li><li>Hours: 8:00AM – 8:00 PM</li>
  </ul>
  <div class="socials" aria-label="Social media links"><span></span><span></span><span></span><span></span></div>
  <div class="rule"></div>
  <div class="copy">© Velour Detailing 2025 – All rights reserved</div>
  <div class="to-top"><svg width="14" height="14" viewBox="0 0 14 14"><path d="M7 2v10M3 6l4-4 4 4" stroke="#000" stroke-width="1.5" fill="none"/></svg></div>
</footer>

</body>
</html>
```